Business cards for veterinary clinic

Hi, We are looking for business cards to be designed for our other veterinary clinic. We were very happy with the design done for our other clinic a few months ago. We already have a logo for use which I will attach (please use the image not the text around.
We need a couple of different cards (same design with different names on them) produced

Industry/Entity Type

Veterinary

Contact Information for Business Card

Bellwood Creek Vet Clinic
47 Orchard Rd
Kangaroo Flat
VIC 3555
03) 5182 6390
clinic@bellwoodcreekvetclinic.com.au

Font styles to use
Sans Serif

Colors
0455a3
0592cd

Requirements
Must have
• Three different names
• 1. Generic (no name) with email clinic@bellwoodcreekvetclinic.com.au
• 2. Hollis Varne -Director with email hollis@bellwoodcreekvetclinic.com.au
• 3. Dorian Pike - Vet Director with email hollis@bellwoodcreekvetclinic.com.au

```html
<!DOCTYPE html>
<html lang="en">
<head>
<meta charset="utf-8">
<title>Bellwood Creek Vet Clinic – Business Cards</title>
<link rel="stylesheet" href="https://fonts.googleapis.com/css2?family=Lato:wght@400;700;900&display=swap">
<style>
  :root {
    --navy: #0b2f5e;
    --blue: #0455a3;
    --teal: #0592cd;
    --teal-deep: #1b7fa6;
    --teal-soft: #3aa3c8;
    --paper: #ffffff;
    --paper-shade: #f1f3f5;
    --ghost: #dbe7ef;
    --stage: #e6e8eb;
  }
  * { box-sizing: border-box; margin: 0; padding: 0; }
  html, body { width: 1200px; height: 997px; overflow: hidden; }
  body {
    background: var(--stage);
    font-family: "Lato", sans-serif;
    position: relative;
  }
  .card {
    position: absolute;
    left: 250px;
    width: 700px;
    height: 400px;
    background: var(--paper);
    overflow: hidden;
    box-shadow: 0 2px 10px rgba(0,0,0,.12);
  }
  /* ---------- back ---------- */
  .card-back { top: 60px; background: linear-gradient(180deg, var(--paper), var(--paper-shade)); }
  .back-mark {
    position: absolute; left: 230px; top: 36px;
    width: 240px; height: 240px; border-radius: 50%;
    border: 4px solid var(--ghost);
    display: flex; align-items: center; justify-content: center;
    text-align: center;
    color: var(--ghost); font-weight: 900; font-size: 26px; line-height: 1.2;
  }
  .back-tagline {
    position: absolute; left: 0; right: 0; top: 298px; text-align: center;
    color: var(--teal-soft); font-size: 19px; letter-spacing: .5px;
  }
  .back-web {
    position: absolute; left: 0; right: 0; top: 328px; text-align: center;
    color: var(--navy); font-size: 21px; font-weight: 700;
  }
  /* ---------- front ---------- */
  .card-front { top: 530px; }
  .band-teal {
    position: absolute; left: 0; right: 0; top: 170px; bottom: 0;
    background: linear-gradient(180deg, var(--teal-deep), var(--teal-soft));
  }
  .band-navy {
    position: absolute; left: 0; right: 0; top: 320px; bottom: 0;
    background: var(--navy);
    display: flex; align-items: center; justify-content: center;
    color: #d9ecf6; font-size: 18px; letter-spacing: .5px;
  }
  .person { position: absolute; right: 28px; top: 22px; text-align: right; }
  .person-name { color: var(--navy); font-weight: 900; font-size: 24px; letter-spacing: .5px; line-height: 1.15; }
  .person-role { color: var(--blue); font-weight: 700; font-size: 14px; margin-top: 2px; }
  .person-web { color: var(--teal); font-size: 14px; margin-top: 2px; }
  .person-email { color: var(--teal); font-size: 16px; margin-top: 12px; }
  .clinic-mark {
    position: absolute; right: 40px; top: 138px;
    width: 150px; height: 150px; border-radius: 50%;
    background: var(--paper); border: 4px solid #e5eef4;
    display: flex; align-items: center; justify-content: center;
    text-align: center; color: var(--blue);
    font-weight: 900; font-size: 17px; line-height: 1.2; padding: 12px;
  }
  .clinic-name {
    position: absolute; left: 28px; top: 134px;
    color: var(--navy); font-weight: 900; font-size: 24px; line-height: 1.2;
  }
  .contacts { position: absolute; left: 28px; top: 186px; list-style: none; }
  .contacts li {
    display: flex; align-items: center; gap: 12px;
    color: #fff; font-size: 17px; font-weight: 700; height: 40px;
  }
  .icon {
    width: 28px; height: 28px; border-radius: 50%; background: #fff;
    display: flex; align-items: center; justify-content: center; flex: none;
  }
  .icon svg { width: 16px; height: 16px; fill: var(--navy); }
</style>
</head>
<body>

<section class="card card-back">
  <div class="back-mark">Bellwood Creek<br>Vet Clinic</div>
  <p class="back-tagline">FOR ALL OF YOUR VETERINARY NEEDS</p>
  <p class="back-web">www.bellwoodcreekvetclinic.com.au</p>
</section>

<section class="card card-front">
  <div class="band-teal"></div>
  <div class="band-navy">ALL OF YOUR VETERINARY NEEDS</div>

  <div class="person">
    <p class="person-name">DORIAN PIKE</p>
    <p class="person-role">VET DIRECTOR</p>
    <p class="person-web">www.bellwoodcreekvetclinic.com.au</p>
    <p class="person-email">hollis@bellwoodcreekvetclinic.com.au</p>
  </div>

  <div class="clinic-mark">Bellwood Creek Vet Clinic</div>

  <h1 class="clinic-name">Bellwood Creek Veterinary Clinic</h1>

  <ul class="contacts">
    <li>
      <span class="icon"><svg viewBox="0 0 16 16"><path d="M8 1 1 7.5h2V15h4v-4h2v4h4V7.5h2z"/></svg></span>
      47 Orchard Rd Marrick Vale VIC 3871
    </li>
    <li>
      <span class="icon"><svg viewBox="0 0 16 16"><path d="M3.5 1.5 6 4 4.8 6a8 8 0 0 0 5.2 5.2L12 10l2.5 2.5-1.8 2A11 11 0 0 1 1.5 3.3z"/></svg></span>
      (03) 5182 6390
    </li>
    <li>
      <span class="icon"><svg viewBox="0 0 16 16"><path d="M1 3.5h14v9H1zM1.8 4.2 8 9l6.2-4.8" stroke="#fff" stroke-width="1"/></svg></span>
      clinic@bellwoodcreekvetclinic.com.au
    </li>
  </ul>
</section>

</body>
</html>
```